Personal Business card and maybe logo or graphic?

I would like a card to give out like you would a business card, however I am not promoting a business, it is just for my personal details.

I have no brand and no logo to worry about.

I would like some images or a logo of some kind or a graphic so the card has some excitement about it.

I am happy if you wish to create a logo/graphic that represents my name, I have seen someone with just their initials as a graphic so for me PH, however I am happy for you to create anything you wish, it does not have to relate to me just make the card look fun and still professional.

Please use the details

Peter Hollis

Ashcombe House
9 The Croft
Elm Rise
Bournemouth
Dorset
BH4 2QP

+44 (0)7812 604258
peter@hollispost.com
linkedin.com/in/hollispeter

looking for a mix between fun, fresh , young whilst being professional

I am new to this and am looking for you to guide me through the process please ask questions and ideas

I am just tidying up my brief as I am starting to understand more. hope it has not confused anyone
Updates

Reason: I have not had time to review or comment due to personal issues sorry

Hi,

to help would you be so kind as to use these sample details on the card

I am uk based and a few designs have us details which look different

Peter Hollis

Ashcombe house

9 The Croft

Elm Rise

Bournemouth

Dorset

BH4 2QP

+44 (0)7812 604258

peter@hollispost.com

many thanks hope that is ok and not too much trouble!

regards

Pete

My are of expertise is IT management / IT Consultancy, incase you wish to incorporate any graphics

My job was that of CIO (Chief Information Officer) or another term is Head of IT

just advising incase this gives any assistance as one designer has asked s may be useful to others

thanks                                   

just thought I have had a look and the UK size for a business card seems to be as per below

I thought I would mention as I guess the US size may be different and other countries too

I found these sizes on Cardforge but guess most companies will be similar

that said maybe you can advise me

I have no idea what cardforge is like so not sure where to get cards made, will figure that out later I guess but I assume dimensions are important for the design

thanks

 

Document Trim Size    

            Horizontal        

        85 x 55 mm           

1004 x 650 pixels           

            Vertical        

        55 x 85 mm           

650 x 1004 pixels           

        Full Bleed Size    

            Horizontal        

        88 x 58 mm           

1039 x 685 pixels           

            Vertical        

        58 x 88 mm           

685 x 1039 pixels           

 many thanks

Target Market(s)

Professional and personal contacts

Industry/Entity Type

Business

```html
<!DOCTYPE html>
<html lang="en">
<head>
<meta charset="utf-8">
<title>Peter Hollis – Personal Card</title>
<link rel="stylesheet" href="https://fonts.googleapis.com/css2?family=Jost:wght@300;400&display=swap">
<style>
  :root {
    --canvas: #ecebe8;
    --navy-top: #2f3f95;
    --navy-bottom: #0e1869;
    --navy-ink: #1b2578;
    --paper: #ffffff;
    --white-ink: #ffffff;
    --ornament-light: #c9cde6;
    --ornament-navy: #3a4596;
    --shadow: rgba(0, 0, 0, 0.22);
  }

  html, body {
    margin: 0;
    padding: 0;
    width: 1200px;
    height: 1200px;
    overflow: hidden;
    background: var(--canvas);
  }

  .sheet {
    position: relative;
    width: 1200px;
    height: 1200px;
    font-family: "Jost", "Futura", sans-serif;
  }

  .card {
    position: absolute;
    left: 220px;
    width: 760px;
    height: 492px;
    box-shadow: 0 10px 26px var(--shadow);
    overflow: hidden;
  }

  .card--front {
    top: 80px;
    background: linear-gradient(to bottom, var(--navy-top), var(--navy-bottom));
    color: var(--white-ink);
  }

  .card--back {
    top: 628px;
    background: var(--paper);
    color: var(--navy-ink);
  }

  .monogram {
    position: absolute;
    display: flex;
    align-items: center;
  }

  .monogram__ornament {
    display: block;
  }

  .monogram__initials {
    font-weight: 300;
    line-height: 1;
    letter-spacing: 0.02em;
  }

  .card--front .monogram {
    left: 56px;
    top: 118px;
    gap: 10px;
  }
  .card--front .monogram__ornament { width: 104px; height: 150px; }
  .card--front .monogram__initials { font-size: 150px; }

  .card--back .monogram {
    left: 290px;
    top: 176px;
    gap: 6px;
  }
  .card--back .monogram__ornament { width: 60px; height: 88px; }
  .card--back .monogram__initials { font-size: 88px; }

  .details {
    position: absolute;
    right: 58px;
    top: 100px;
    text-align: right;
  }

  .details__name {
    margin: 0 0 44px;
    font-size: 44px;
    font-weight: 400;
    letter-spacing: 0.01em;
  }

  .details__line {
    margin: 0;
    font-size: 28px;
    font-weight: 400;
    line-height: 1.3;
    letter-spacing: 0.02em;
  }
</style>
</head>
<body>
<main class="sheet">

  <section class="card card--front" aria-label="Card front">
    <div class="monogram">
      <svg class="monogram__ornament" viewBox="0 0 104 150" role="img" aria-label="Floral flourish ornament">
        <rect x="0" y="0" width="104" height="150" fill="var(--ornament-light)"/>
      </svg>
      <span class="monogram__initials">PH</span>
    </div>

    <div class="details">
      <h1 class="details__name">Peter Hollis</h1>
      <p class="details__line">07812 604258</p>
      <p class="details__line">peter@hollispost.com</p>
      <p class="details__line">9 The Croft, Elm Rise</p>
    </div>
  </section>

  <section class="card card--back" aria-label="Card back">
    <div class="monogram">
      <svg class="monogram__ornament" viewBox="0 0 60 88" role="img" aria-label="Floral flourish ornament">
        <rect x="0" y="0" width="60" height="88" fill="var(--ornament-navy)"/>
      </svg>
      <span class="monogram__initials">PH</span>
    </div>
  </section>

</main>
</body>
</html>
```